Brisbane IT support business needs our first website

Hi All,

We are after a new website design for our IT solutions and support business.The business name is Harbourline Computing Services Group, or HCSG for short. We provide a range of solutions and services within the IT space.

I would like to utilize the two colours in our business logo I have uploaded.

I understand this is initially for the design only aspect of the site, but I would like to engage the winner to finish coding the website and finalize after also.

Target Market(s)

Other businesses owners and home users.

Industry/Entity Type

Business

Requirements
Must have
• Nice clean and functional design utilizing our business colours from the logo.

```html
<!DOCTYPE html>
<html lang="en">
<head>
<meta charset="utf-8">
<title>HCSG – IT Solutions</title>
<link rel="stylesheet" href="https://fonts.googleapis.com/css2?family=Oswald:wght@500;600&family=Montserrat:ital,wght@0,600;0,700;1,400&family=Open+Sans:wght@400;600&display=swap">
<style>
:root{
  --navy:#0c3150;
  --navy-deep:#0a2b47;
  --orange:#f26522;
  --ink:#474747;
  --white:#ffffff;
  --sky-1:#bfe3f7;
  --sky-2:#5fb2e6;
  --sky-3:#2a7fc0;
}
*{margin:0;padding:0;box-sizing:border-box}
html,body{width:1200px;height:2853px;overflow:hidden;background:var(--white)}
body{position:relative;font-family:"Open Sans",Arial,sans-serif;color:var(--ink)}
h1,h2,h3{line-height:1}
.abs{position:absolute}
.center{left:0;width:1200px;text-align:center}

/* hero */
.hero{left:0;top:0;width:1200px;height:563px;overflow:hidden}
.hero-photo{position:absolute;inset:0;background:radial-gradient(circle at 880px 160px,#e6f6ff 0,var(--sky-1) 18%,var(--sky-2) 50%,var(--sky-3) 100%)}
.brand-name{left:53px;top:78px;font-family:"Open Sans",Arial,sans-serif;font-weight:600;font-size:30px;line-height:36px;color:var(--navy)}
.nav{top:127px;left:0;width:1200px;font-family:"Montserrat",Arial,sans-serif;font-weight:600;font-size:14px;color:var(--navy)}
.nav span{position:absolute;white-space:nowrap}
.nav .active{color:var(--orange)}
.hero-title{top:236px;font-family:"Oswald",Arial,sans-serif;font-weight:600;font-size:80px;color:var(--navy);letter-spacing:1px}
.hero-sub{top:336px;font-family:"Montserrat",Arial,sans-serif;font-weight:700;font-size:21px;line-height:24px;color:#0b2438}
.quote-btn{left:496px;top:398px;width:206px;height:60px;background:var(--orange);color:var(--white);font-family:"Montserrat",Arial,sans-serif;font-weight:700;font-size:14px;display:flex;align-items:center;justify-content:center;border-radius:3px}

/* shared headings */
.kicker{font-family:"Oswald",Arial,sans-serif;font-weight:600;font-size:33px;color:var(--orange)}
.rule{left:549px;width:102px;height:4px;background:linear-gradient(90deg,transparent,#f7c6ad 25%,var(--orange) 40%,var(--orange) 60%,#f7c6ad 75%,transparent)}

/* about */
.about-title{top:718px;font-family:"Oswald",Arial,sans-serif;font-weight:500;font-size:66px;line-height:74px;letter-spacing:-1.5px;color:var(--ink)}
.about-text{left:53px;top:901px;width:1094px;text-align:center;font-size:12.5px;line-height:22px;color:var(--ink)}

/* services */
.services{left:0;top:1040px;width:1200px;height:955px;background:var(--navy)}
.notch{left:0;width:1200px;height:56px}
.section-title{font-family:"Oswald",Arial,sans-serif;font-weight:600;font-size:38px;color:var(--white)}
.service{width:405px;color:var(--white)}
.service-icon{position:absolute;left:-128px;top:-10px;width:92px;height:92px}
.service.right .service-icon{left:-112px}
.service h3{font-family:"Montserrat",Arial,sans-serif;font-weight:700;font-size:26px;line-height:34px;white-space:nowrap}
.service em{display:block;font-family:"Montserrat",Arial,sans-serif;font-style:italic;font-weight:400;font-size:18px;line-height:22px;margin-top:4px}
.service p{font-size:13px;line-height:20px;margin-top:14px;padding-left:4px}

/* testimonial */
.testimonial-text{left:120px;top:2189px;width:960px;text-align:center;font-size:12.5px;line-height:21px;color:var(--ink)}
.qmark{font-family:Georgia,serif;font-size:48px;color:#bdbdbd;line-height:1}

/* contact */
.contact{left:0;top:2343px;width:1200px;height:396px;background:var(--navy);color:var(--white)}
.contact-lead{top:2501px;font-size:16px;line-height:27px;color:var(--white)}
.col-title{top:2598px;font-family:"Montserrat",Arial,sans-serif;font-weight:700;font-size:27px;color:var(--white)}
.col-text{font-size:12.5px;line-height:21px;color:var(--white)}
.social{width:36px;height:36px;border:2px solid var(--white);border-radius:50%;top:2642px}
.footer{left:0;top:2740px;width:1200px;height:113px;background:var(--navy-deep);color:var(--white);font-size:12px;text-align:center;padding-top:50px}
</style>
</head>
<body>

<header class="abs hero">
  <div class="hero-photo" role="img" aria-label="Hand touching a glowing digital globe above a city skyline on a light blue technology background"></div>
  <span class="abs brand-name">HCSG</span>
  <nav class="abs nav">
    <span class="active" style="left:603px">HOME</span>
    <span style="left:683px">ABOUT</span>
    <span style="left:768px">SERVICES</span>
    <span style="left:867px">TEAM</span>
    <span style="left:945px">PORTFOLIO</span>
    <span style="left:1059px">CONTACT US</span>
  </nav>
  <h1 class="abs center hero-title">IT SOLUTIONS</h1>
  <p class="abs center hero-sub">IT NEEDS CHANGE ALL THE TIME. WE ARE HERE TO CONNECT THE DOTS.</p>
  <a class="abs quote-btn">REQUEST A FREE QUOTE</a>
</header>

<section>
  <h2 class="abs center kicker" style="top:608px">ABOUT US</h2>
  <div class="abs rule" style="top:664px"></div>
  <h2 class="abs center about-title">INFORMATION TECHNOLOGY<br>SOLUTIONS</h2>
  <p class="abs about-text">Sed ut perspiciatis unde omnis iste natus error sit voluptatem accusantium doloremque laudantium, totam rem aperiam, eaque ipsa quae ab illo inventore veritatis et quasi architecto beatae vitae dicta sunt explicabo. Nemo enim ipsam voluptatem quia voluptas sit aspernatur aut odit aut fugit, sed quia consequuntur magni dolores eos qui ratione voluptatem sequi nesciunt. Neque porro quisquam est, qui dolorem ipsum quia dolor sit amet, consectetur, adipisci velit.</p>
</section>

<section class="abs services">
  <svg class="abs notch" style="top:0" viewBox="0 0 1200 56"><polygon points="480,0 720,0 600,56" fill="#fff"/></svg>
  <h2 class="abs center section-title" style="top:163px">SERVICES WE PROVIDE</h2>

  <div class="abs service" style="left:179px;top:281px">
    <svg class="service-icon" viewBox="0 0 92 92" fill="none" stroke="#fff" stroke-width="4"><path d="M22 66h50a14 14 0 0 0 0-28 20 20 0 0 0-38-6 16 16 0 0 0-12 34z"/></svg>
    <h3>CLOUD &amp; HOSTING</h3><em>LET MAKE SOMETHING NEW</em>
    <p>Lorem ipsum dolor sit amet, consectetur adipiscing elit, sed do eiusmod tempor incididunt ut labore et dolore magna aliqua. Ut enim ad minim veniam, quis nostrud exercitation ullamco laboris nisi</p>
  </div>
  <div class="abs service right" style="left:744px;top:281px">
    <svg class="service-icon" viewBox="0 0 92 92" fill="none" stroke="#fff" stroke-width="4"><circle cx="46" cy="30" r="16"/><path d="M16 78c2-18 14-26 30-26s28 8 30 26z"/></svg>
    <h3>MANAGED SERVICES</h3><em>LET MAKE SOMETHING NEW</em>
    <p>Lorem ipsum dolor sit amet, consectetur adipiscing elit, sed do eiusmod tempor incididunt ut labore et dolore magna aliqua. Ut enim ad minim veniam, quis nostrud exercitation ullamco laboris nisi</p>
  </div>

  <div class="abs service" style="left:179px;top:487px">
    <svg class="service-icon" viewBox="0 0 92 92" fill="#fff" stroke="#fff" stroke-width="3"><circle cx="46" cy="46" r="12"/><path d="M46 46L46 14M46 46L46 78M46 46L14 46M46 46L78 46M46 46L23 23M46 46L69 69M46 46L69 23M46 46L23 69"/><circle cx="46" cy="12" r="6"/><circle cx="46" cy="80" r="6"/><circle cx="12" cy="46" r="6"/><circle cx="80" cy="46" r="6"/><circle cx="22" cy="22" r="5"/><circle cx="70" cy="70" r="5"/><circle cx="70" cy="22" r="5"/><circle cx="22" cy="70" r="5"/></svg>
    <h3>ERP APPLICATION</h3><em>LET MAKE SOMETHING NEW</em>
    <p>Lorem ipsum dolor sit amet, consectetur adipiscing elit, sed do eiusmod tempor incididunt ut labore et dolore magna aliqua. Ut enim ad minim veniam, quis nostrud exercitation ullamco laboris nisi</p>
  </div>
  <div class="abs service right" style="left:744px;top:487px">
    <svg class="service-icon" viewBox="0 0 92 92" fill="none" stroke="#fff" stroke-width="4"><circle cx="46" cy="30" r="17"/><path d="M12 80c2-20 16-28 34-28s32 8 34 28z"/></svg>
    <h3>PROFESSIONAL SERVICES</h3><em>LET MAKE SOMETHING NEW</em>
    <p>Lorem ipsum dolor sit amet, consectetur adipiscing elit, sed do eiusmod tempor incididunt ut labore et dolore magna aliqua. Ut enim ad minim veniam, quis nostrud exercitation ullamco laboris nisi</p>
  </div>

  <div class="abs service" style="left:179px;top:688px">
    <svg class="service-icon" viewBox="0 0 92 92" fill="#fff"><path d="M6 46h68v28H6z"/><path d="M12 30h40v14H6z"/><rect x="56" y="60" width="12" height="4" fill="#0c3150"/><path d="M58 30h28a9 9 0 0 0 0-18 13 13 0 0 0-24-2 10 10 0 0 0-4 20z" stroke="#0c3150" stroke-width="3"/></svg>
    <h3>IT HARDWARE</h3><em>LET MAKE SOMETHING NEW</em>
    <p>Lorem ipsum dolor sit amet, consectetur adipiscing elit, sed do eiusmod tempor incididunt ut labore et dolore magna aliqua. Ut enim ad minim veniam, quis nostrud exercitation ullamco laboris nisi</p>
  </div>
  <div class="abs service right" style="left:744px;top:688px">
    <svg class="service-icon" viewBox="0 0 92 92" fill="none" stroke="#fff" stroke-width="4"><path d="M20 6h38l16 16v64H20z"/><path d="M30 36h34M30 46h34M30 56h34M30 66h34M30 76h34"/><path d="M36 20l-5 5 5 5M52 20l5 5-5 5M46 18l-4 14"/></svg>
    <h3>DATA CENTERS</h3><em>LET MAKE SOMETHING NEW</em>
    <p>Lorem ipsum dolor sit amet, consectetur adipiscing elit, sed do eiusmod tempor incididunt ut labore et dolore magna aliqua. Ut enim ad minim veniam, quis nostrud exercitation ullamco laboris nisi</p>
  </div>
</section>

<section>
  <h2 class="abs center kicker" style="top:2074px">OUR TESTIMONIAL</h2>
  <div class="abs rule" style="top:2146px"></div>
  <span class="abs qmark" style="left:84px;top:2186px">&ldquo;</span>
  <p class="abs testimonial-text">Sed ut perspiciatis unde omnis iste natus error sit voluptatem accusantium doloremque laudantium, totam rem aperiam, eaque ipsa quae ab illo inventore veritatis et quasi architecto beatae vitae dicta sunt explicabo. Nemo enim ipsam voluptatem quia voluptas sit aspernatur aut odit aut fugit, sed quia consequuntur magni dolores eos qui ratione voluptatem sequi nesciunt. Neque porro quisquam est, qui dolorem ipsum quia dolor sit amet, consectetur, adipisci velit,</p>
  <span class="abs qmark" style="left:1050px;top:2238px">&rdquo;</span>
</section>

<section class="abs contact">
  <svg class="abs notch" style="top:0" viewBox="0 0 1200 56"><polygon points="480,0 720,0 600,54" fill="#fff"/></svg>
</section>
<h2 class="abs center section-title" style="top:2447px">CONTACT US</h2>
<p class="abs center contact-lead">If you are looking for a solid partner for your projects, send us an email.<br>We'd love to talk to you!</p>

<h3 class="abs col-title" style="left:51px">GENERAL</h3>
<p class="abs col-text" style="left:51px;top:2642px">14 Quayside Lane, Harbour Point<br>Bayview, 4102, AU</p>

<h3 class="abs col-title" style="left:400px;width:400px;text-align:center">TOUCH</h3>
<p class="abs col-text" style="left:400px;width:400px;top:2644px;text-align:center">555.014.2290<br>055-410.72.3318<br>hello@hcsg-example.net</p>

<h3 class="abs col-title" style="left:896px;width:300px;text-align:center">CONNECT</h3>
<span class="abs social" style="left:920px" aria-label="Social link 1"></span>
<span class="abs social" style="left:967px" aria-label="Social link 2"></span>
<span class="abs social" style="left:1014px" aria-label="Social link 3"></span>
<span class="abs social" style="left:1061px" aria-label="Social link 4"></span>
<span class="abs social" style="left:1108px" aria-label="Social link 5"></span>

<footer class="abs footer">ALL RIGHTS RESERVED © 2014 HCSG</footer>

</body>
</html>
```